Tidemark Builders Business Card Design

We need a business card for an established builder of high quality bespoke homes in Auckland and Northland. We build and renovate homes collaboratively facilitating effective communication between owners, builders, architects, suppliers and tradespeople. We have never built or renovated a home that leaks or has faults. We only use reliable materials. We have never been sued or had legal action taken against us. We are honest builders of bespoke homes not group mass produced homes. Our niche market is in character homes. We practice sustainability and have built a lot of coastal property. We have been in business for over thirty years . We would like to see natural colors of the environment sand,sea and maybe vegetation . The design should communicate quality, sustainability,fair pricing, open communication and the originality of bespoke building. And the fact that the builder is registered.

Industry/Entity Type

Business

Contact Information for Business Card

Rowan Tellick Builders
Ph. 021583917
18 Kestrel Rd Harwood Bay Auckland 0814
PO Box 927 Mangawhai 0583

```html
<!DOCTYPE html>
<html lang="en">
<head>
<meta charset="utf-8">
<title>Tidemark Builders Business Card</title>
<link href="https://fonts.googleapis.com/css2?family=Source+Sans+3:wght@400;600&family=Mulish:wght@400;600&display=swap" rel="stylesheet">
<style>
  :root {
    --stage: #000000;
    --card-light: #f2f2f2;
    --brand-blue: #2f67bf;
    --blue-deep: #2459ac;
    --blue-soft: #3c78c8;
    --ink: #1a1a1a;
    --white: #ffffff;
  }
  * { margin: 0; padding: 0; box-sizing: border-box; }
  html, body {
    width: 1200px; height: 900px; overflow: hidden;
    background: var(--stage);
  }
  .stage { position: relative; width: 1200px; height: 900px; }

  .card { position: absolute; top: 200px; height: 502px; width: 310px; }

  .card-front {
    left: 265px;
    background: var(--card-light);
    border-radius: 52px 0 52px 0;
  }
  .card-back {
    left: 641px; width: 308px;
    border-radius: 0 52px 0 52px;
    background: radial-gradient(circle at 55% 45%, var(--blue-soft) 0%, var(--brand-blue) 45%, var(--blue-deep) 100%);
  }

  .brand-mark {
    position: absolute; left: 0; width: 100%; text-align: right;
    font-family: "Mulish", sans-serif; font-weight: 600;
    color: var(--brand-blue); line-height: 1;
  }
  .card-front .brand-mark { top: 40px; right: 30px; width: auto; left: auto; }
  .brand-dot {
    display: block; width: 56px; height: 56px; border-radius: 50%;
    background: var(--brand-blue); margin: 0 55px 26px auto;
  }
  .brand-name { display: block; font-size: 42px; letter-spacing: -0.5px; }
  .brand-sub { display: block; font-size: 19px; letter-spacing: 2.5px; margin-top: 6px; }

  .card-back .brand-mark {
    top: auto; bottom: 42px; right: 44px; left: auto; width: auto;
    color: var(--white);
  }
  .card-back .brand-name { font-size: 50px; }
  .card-back .brand-sub { font-size: 21px; letter-spacing: 3px; margin-top: 8px; }

  .contact {
    position: absolute; left: 23px; top: 334px;
    font-family: "Source Sans 3", sans-serif; color: var(--ink);
  }
  .contact-name {
    font-size: 18px; font-weight: 600; color: var(--brand-blue);
    margin-bottom: 14px;
  }
  .contact-phone {
    display: flex; align-items: center; gap: 5px;
    font-size: 14px; margin-bottom: 18px;
  }
  .contact-phone svg { width: 10px; height: 10px; fill: var(--brand-blue); }
  .contact-address { font-size: 14px; line-height: 21px; }
</style>
</head>
<body>
<main class="stage">
  <section class="card card-front" aria-label="Card front">
    <div class="brand-mark">
      <span class="brand-dot" aria-hidden="true"></span>
      <span class="brand-name">Tidemark</span>
      <span class="brand-sub">BUILDERS</span>
    </div>
    <div class="contact">
      <p class="contact-name">Rowan Tellick Builders</p>
      <p class="contact-phone">
        <svg viewBox="0 0 24 24" aria-hidden="true"><path d="M6.6 10.8a15.1 15.1 0 0 0 6.6 6.6l2.2-2.2a1 1 0 0 1 1-.25 11.4 11.4 0 0 0 3.6.57 1 1 0 0 1 1 1V20a1 1 0 0 1-1 1A17 17 0 0 1 3 4a1 1 0 0 1 1-1h3.5a1 1 0 0 1 1 1c0 1.25.2 2.45.57 3.57a1 1 0 0 1-.25 1z"/></svg>
        <span>021583917</span>
      </p>
      <address class="contact-address" style="font-style:normal">
        18 Kestrel Rd Harwood Bay<br>
        Auckland 0814<br>
        PO Box 927 Mangawhai 0583
      </address>
    </div>
  </section>

  <section class="card card-back" aria-label="Card back">
    <div class="brand-mark">
      <span class="brand-name">Tidemark</span>
      <span class="brand-sub">BUILDERS</span>
    </div>
  </section>
</main>
</body>
</html>
```